R7M Horizon Business Card Design

We need a business card created for our New Business "R7M Horizon"<br/><br/>The business card design is up to you however the following information must be on the business card:<br/><br/>Front of the business card -<br/>Email :darrenp@r7mhorizon.nz<br/>Mobile: +64 (0) 22 4870 619<br/>Website: www.r7mhorizon.nz<br/>Card Owner Name: Darren Paltrow<br/>Company Title: Business Development Manager<br/>Slogan: "The BEST of both worlds". <br/>Logo On the front attached to the design brief<br/><br/>On the back: <br/>Space on the back for 4 more versions of the logo across the bottom of the card indicating different subsidiary brands - R7M Coffee, R7M Arts, R7M ?? (The card will be used for all of these brands - We Will add the extra subsidiary logos to the design once the design is finished (We are a graphics design team). <br/><br/>Other than that we want a premium feeling logo that remains universally usable depending on the business entity that we are using the card for. The use of bright bold colours would be great but we still want the card to feel premium.
Target Market(s)
Gift Design and Manufacturing Companies
Contact Information for Business Card
Front of the business card -
Email :darrenp@r7mhorizon.nz
Mobile: +64 (0) 22 4870 619
Website: www.r7mhorizon.nz
Card Owner Name: Darren Paltrow
Company Title: Business Development Manager
Slogan: "The BEST of both worlds".
Logo On the front attached to the design brief

```html
<!DOCTYPE html>
<html lang="en">
<head>
<meta charset="utf-8">
<title>R7M Horizon Business Card</title>
<link href="https://fonts.googleapis.com/css2?family=Open+Sans:wght@400;600;700&display=swap" rel="stylesheet">
<style>
  :root {
    --bg: #d6d6d6;
    --brand-blue: #33479c;
    --brand-blue-deep: #2a3c88;
    --brand-blue-faint: #4759a8;
    --ink: #333333;
    --paper: #ffffff;
  }
  * { box-sizing: border-box; margin: 0; padding: 0; }
  html, body { width: 1200px; height: 900px; overflow: hidden; }
  body {
    background: var(--bg);
    font-family: "Open Sans", Arial, sans-serif;
    position: relative;
  }
  .card {
    position: absolute;
    width: 560px;
    height: 320px;
    box-shadow: 0 6px 18px rgba(0,0,0,0.18);
  }
  /* Back */
  .card-back {
    left: 70px;
    top: 80px;
    background: var(--brand-blue);
  }
  .back-wordmark {
    position: absolute;
    left: 60px;
    top: 120px;
    display: flex;
    align-items: center;
    gap: 16px;
    color: var(--brand-blue-faint);
    font-weight: 700;
    font-size: 46px;
    letter-spacing: 1px;
  }
  .back-wordmark .mark-circle {
    width: 56px; height: 56px;
    border: 5px solid var(--brand-blue-faint);
    border-radius: 50%;
  }
  .subsidiary-list {
    position: absolute;
    right: 26px;
    top: 24px;
    display: flex;
    flex-direction: column;
    gap: 22px;
    list-style: none;
  }
  .subsidiary {
    display: flex;
    align-items: center;
    justify-content: flex-end;
    gap: 8px;
    color: var(--paper);
    font-weight: 700;
    font-size: 15px;
    letter-spacing: 0.5px;
    height: 48px;
  }
  .subsidiary .mark-circle {
    width: 26px; height: 26px;
    border: 3px solid var(--paper);
    border-radius: 50%;
  }
  /* Front */
  .card-front {
    left: 570px;
    top: 500px;
    background: var(--paper);
  }
  .front-wordmark {
    position: absolute;
    left: 0; right: 0;
    top: 46px;
    display: flex;
    justify-content: center;
    align-items: center;
    gap: 12px;
    color: var(--brand-blue);
    font-weight: 700;
    font-size: 34px;
    letter-spacing: 0.5px;
  }
  .front-wordmark .mark-circle {
    width: 44px; height: 44px;
    border: 4px solid var(--brand-blue);
    border-radius: 50%;
  }
  .details {
    position: absolute;
    left: 0; right: 0;
    top: 130px;
    display: flex;
    justify-content: center;
    align-items: stretch;
    gap: 18px;
  }
  .person { text-align: right; padding-top: 20px; }
  .person-name {
    color: var(--brand-blue);
    font-weight: 700;
    font-size: 17px;
    text-transform: uppercase;
    letter-spacing: 0.3px;
  }
  .person-title {
    color: var(--ink);
    font-size: 12.5px;
    line-height: 1.3;
  }
  .divider { width: 1px; background: var(--ink); height: 76px; }
  .contacts { list-style: none; font-size: 12.5px; color: var(--ink); line-height: 1.55; }
  .contacts li { display: flex; align-items: center; gap: 6px; }
  .contacts svg { width: 11px; height: 11px; flex: none; }
  .slogan-rule {
    position: absolute;
    left: 40px; right: 40px;
    bottom: 42px;
    display: flex;
    align-items: center;
    gap: 12px;
  }
  .slogan-rule .rule { flex: 1; height: 1px; background: var(--brand-blue); }
  .slogan {
    color: var(--brand-blue);
    font-size: 13px;
    text-transform: uppercase;
    letter-spacing: 0.3px;
    white-space: nowrap;
  }
</style>
</head>
<body>
  <section class="card card-back" aria-label="Card back">
    <div class="back-wordmark"><span>R7M Horizon</span><span class="mark-circle"></span></div>
    <ul class="subsidiary-list">
      <li class="subsidiary"><span>R7M Coffee</span><span class="mark-circle"></span></li>
      <li class="subsidiary"><span>R7M Arts</span><span class="mark-circle"></span></li>
      <li class="subsidiary"><span>R7M Coffee</span><span class="mark-circle"></span></li>
      <li class="subsidiary"><span>R7M Arts</span><span class="mark-circle"></span></li>
    </ul>
  </section>

  <section class="card card-front" aria-label="Card front">
    <div class="front-wordmark"><span>R7M Horizon</span><span class="mark-circle"></span></div>
    <div class="details">
      <div class="person">
        <p class="person-name">Darren Paltrow</p>
        <p class="person-title">Business Development<br>Manager</p>
      </div>
      <div class="divider"></div>
      <ul class="contacts">
        <li>
          <svg viewBox="0 0 12 12" aria-hidden="true"><rect x="2.5" y="0.5" width="7" height="11" rx="1.2" fill="none" stroke="#33479c"/><line x1="5" y1="9.5" x2="7" y2="9.5" stroke="#33479c"/></svg>
          <span>+64 (0) 22 4870 619</span>
        </li>
        <li>
          <svg viewBox="0 0 12 12" aria-hidden="true"><rect x="0.5" y="2" width="11" height="8" fill="none" stroke="#33479c"/><polyline points="0.5,2 6,7 11.5,2" fill="none" stroke="#33479c"/></svg>
          <span>darrenp@r7mhorizon.nz</span>
        </li>
        <li>
          <svg viewBox="0 0 12 12" aria-hidden="true"><circle cx="6" cy="6" r="5.5" fill="#33479c"/><line x1="0.5" y1="6" x2="11.5" y2="6" stroke="#fff" stroke-width="0.8"/><ellipse cx="6" cy="6" rx="2.4" ry="5.5" fill="none" stroke="#fff" stroke-width="0.8"/></svg>
          <span>www.r7mhorizon.nz</span>
        </li>
      </ul>
    </div>
    <div class="slogan-rule">
      <span class="rule"></span>
      <span class="slogan">The Best of Both Worlds</span>
      <span class="rule"></span>
    </div>
  </section>
</body>
</html>
```